Business Card (double-sided) and Stationary Design for dental office

1) Business Card Design: We need a business card design for a dental specialty office.
Texts should contain:
The name of our office "Brindle Oaks Orthodontics"
Tagline: "Specialist in Orthodontic and Maxillofacial Orthopedics"
Tag line: "Creating "Tolvering" smiles for Children and Adults"
Doctor name: "Doctor Name"
Office Address:
"123 Street Name
City, State Zip code"
Office email address: office@brindleoaksortho.com
Website: www.brindleoaksortho.com

We will provide the full office address once the design is selected
Theme: beach, paradise, coastal, wave
We would like to have some creativity in design. Some acceptable ideas: front page: logo and office name. Back page: more detail information, and map to office in form of an island. Please see sample from our other location, but you DON'T HAVE TO USE OR COPY THE SAME CONCEPT.

IF POSSIBLE, PLEASE SUBMIT AT LEAST TWO CONCEPTS: ONE WITH THE BACK LOOKING SIMILAR TO WHAT IS IN THE SAMPLE, AND ONE DIFFERENT.

Color: designer to choose. We have different shade of blues and sand color in our office. Please see logo.

2) Please also design a matching set of stationary that compliment the business card and our logo.

Target Market(s)

Dental

Contact Information for Business Card

See descriptions

Font styles to use
Other font styles liked:
• Matching texts in logo

Colors
0054AA
0677BA
7BADD7
CADEEF
E8F1F8
0094D4
00A9DD
6FCCEA
C7EBF8
E9F6FB
00AB8E
00BBA5
67D7C9
C6EFE9
E9F9F6

Requirements
Must have
• Double-sided
Nice to have
• Beach coastal theme
Should not have
• Any shape or drawing of of tooth or teeth. We don’t need these. You don't necessarily have to just cut and paste the logo art and text as a whole, you have the liberty to rearrange the text.

```html
<!DOCTYPE html>
<html lang="en">
<head>
<meta charset="utf-8">
<title>Brindle Oaks Orthodontics — Stationery Set</title>
<link href="https://fonts.googleapis.com/css2?family=Open+Sans:ital,wght@0,400;0,600;0,700;1,700&display=swap" rel="stylesheet">
<style>
  :root {
    --backdrop: #969393;
    --paper: #f4f4f5;
    --paper-white: #ffffff;
    --teal: #3a8ca5;
    --teal-dark: #2f7d96;
    --mint: #6cc4b8;
    --ink: #555a5e;
    --ink-soft: #8a8f93;
    --ghost: rgba(58, 140, 165, 0.10);
  }
  * { box-sizing: border-box; margin: 0; padding: 0; }
  html, body { width: 1200px; height: 826px; overflow: hidden; }
  body {
    background: var(--backdrop);
    font-family: "Open Sans", sans-serif;
    position: relative;
    color: var(--ink);
  }
  .piece {
    position: absolute;
    overflow: hidden;
    box-shadow: 0 1px 4px rgba(0,0,0,0.25);
  }

  /* Brand lockup */
  .brand { display: flex; flex-direction: column; align-items: center; }
  .brand__dot { border-radius: 50%; background: var(--teal); }
  .brand__name { font-weight: 600; color: var(--teal); line-height: 1.1; white-space: nowrap; }
  .brand__tag { font-weight: 600; color: var(--mint); letter-spacing: 0.6px; white-space: nowrap; }

  .ghost-ring {
    position: absolute; border-radius: 50%;
    border: 14px solid var(--ghost);
  }

  /* Letterhead */
  .letterhead { left: 60px; top: 111px; width: 462px; height: 646px; background: linear-gradient(90deg, #f7f7f8, #efeff0); }
  .letterhead .brand { position: absolute; left: 0; right: 0; top: 34px; }
  .letterhead .brand__dot { width: 46px; height: 46px; }
  .letterhead .brand__name { font-size: 16px; margin-top: 8px; }
  .letterhead .brand__tag { font-size: 5.5px; }
  .letterhead .ghost-ring { left: 126px; top: 200px; width: 212px; height: 212px; border-width: 22px; }
  .letter { position: absolute; left: 41px; top: 186px; width: 384px; }
  .letter__salutation { font-size: 11.5px; color: #4a4e52; margin-bottom: 16px; }
  .letter p { font-size: 6.3px; line-height: 10px; color: var(--ink-soft); margin-bottom: 9px; text-align: justify; }
  .letter__closing { margin-top: 18px; font-size: 6.5px; color: var(--ink-soft); }
  .footer-band {
    position: absolute; left: 0; right: 0; height: 30px; background: var(--teal);
    color: #fff; font-size: 8.8px; line-height: 11.5px; padding: 4px 0 0 40px;
  }
  .letterhead .footer-band { top: 582px; }
  .footer-band .badge {
    position: absolute; right: 44px; top: -2px; width: 34px; height: 34px; border-radius: 50%;
    background: var(--paper-white); border: 3px solid var(--teal);
  }

  /* Business card front */
  .card { width: 288px; height: 165px; top: 120px; }
  .card--contact { left: 550px; background: var(--teal); }
  .card--contact svg { position: absolute; inset: 0; }
  .card__details { position: absolute; left: 18px; top: 37px; color: #fff; }
  .card__name { font-weight: 700; font-size: 9.5px; letter-spacing: 0.3px; margin-bottom: 6px; }
  .card__line { font-size: 6.2px; line-height: 8px; }
  .card__contact { margin-top: 6px; }
  .card__contact div { display: flex; align-items: center; gap: 4px; font-size: 6.2px; line-height: 8.3px; }
  .card__contact svg { position: static; width: 6px; height: 6px; }
  .card__slogan { margin-top: 8px; font-size: 6px; font-weight: 700; font-style: italic; line-height: 8px; }
  .card--contact .brand { position: absolute; left: 160px; top: 50px; width: 120px; }
  .card--contact .brand__dot { width: 40px; height: 40px; }
  .card--contact .brand__name { font-size: 13px; margin-top: 6px; }
  .card--contact .brand__tag { font-size: 4.6px; }

  /* Appointment card */
  .card--appointment { left: 862px; background: var(--paper-white); }
  .island {
    position: absolute; left: 0; top: 0; width: 150px; height: 165px;
    background:
      linear-gradient(180deg, rgba(255,255,255,0) 0%, rgba(255,255,255,0) 55%, #f2c86c 62%, #e9b450 82%, #3fb3d7 92%, #2a9cc8 100%),
      radial-gradient(circle at 40% 30%, #5fae3a 0%, #4a8f2c 25%, rgba(255,255,255,0) 45%);
  }
  .appt__title { position: absolute; right: 12px; top: 18px; font-weight: 700; font-size: 8px; color: var(--teal-dark); }
  .appt__field { position: absolute; font-size: 6px; color: var(--ink); display: flex; align-items: flex-end; gap: 2px; }
  .appt__field span.rule { display: block; border-bottom: 1px dotted #999; height: 6px; }
  .appt__pill {
    position: absolute; left: 126px; top: 83px; width: 150px; height: 11px; border-radius: 6px;
    background: var(--teal); color: #fff; font-size: 5.2px; font-weight: 700; font-style: italic;
    display: flex; align-items: center; justify-content: center; white-space: nowrap;
  }
  .card--appointment .brand { position: absolute; left: 145px; top: 100px; width: 140px; }
  .card--appointment .brand__dot { width: 40px; height: 40px; }
  .card--appointment .brand__name { font-size: 13px; margin-top: 3px; }
  .card--appointment .brand__tag { font-size: 4.6px; }

  /* Envelopes */
  .envelope { width: 530px; background: linear-gradient(90deg, #f7f7f8, #efeff0); }
  .envelope--back { left: 602px; top: 337px; height: 240px; }
  .envelope--back svg { position: absolute; left: 0; top: 0; }
  .envelope--back .flap-mark {
    position: absolute; left: 230px; top: 16px; width: 46px; height: 46px; border-radius: 50%;
    background: var(--paper-white);
  }
  .envelope--front { left: 565px; top: 510px; height: 242px; }
  .envelope--front .brand { position: absolute; left: 25px; top: 28px; width: 150px; }
  .envelope--front .brand__dot { width: 46px; height: 46px; }
  .envelope--front .brand__name { font-size: 15px; margin-top: 8px; }
  .envelope--front .brand__tag { font-size: 5.2px; }
  .envelope--front .ghost-ring { left: 312px; top: 84px; width: 184px; height: 184px; border-width: 20px; }
  .envelope--front .footer-band { top: 184px; padding-left: 26px; font-size: 8.8px; }
  .envelope--front .footer-band .badge { right: 52px; }
</style>
</head>
<body>

  <!-- Letterhead -->
  <section class="piece letterhead">
    <div class="ghost-ring"></div>
    <div class="brand">
      <div class="brand__dot"></div>
      <div class="brand__name">Brindle Oaks</div>
      <div class="brand__tag">Pediatric Dentistry &amp; Orthodontics</div>
    </div>
    <div class="letter">
      <div class="letter__salutation">Dear Mr. Ferro,</div>
      <p>Thank you for choosing our practice for your family's care. We are writing to confirm the details of your upcoming visit and to share a few notes about what to expect. Please arrive ten minutes early so our team can review your forms and answer any questions before the exam begins.</p>
      <p>During the visit we will take new records, check how treatment is progressing and talk through the next steps together. If anything has changed in your health since your last appointment, let us know so we can update your file and plan around it.</p>
      <p>Our office offers early morning and late afternoon times for busy families. Should you need to move your appointment, please call at least one day ahead so we can offer the slot to another patient waiting for care.</p>
      <p>We look forward to seeing you soon and to helping you build a healthy, confident smile that lasts for years.</p>
      <div class="letter__closing">Sincerely,</div>
    </div>
    <div class="footer-band">
      Brindle Oaks Orthodontics 123 Street Name, City, State Zip code<br>
      P. 555-014-2273 E. office@brindleoaksortho.com W. brindleoaksortho.com
      <div class="badge"></div>
    </div>
  </section>

  <!-- Business card -->
  <section class="piece card card--contact">
    <svg width="288" height="165" viewBox="0 0 288 165">
      <path d="M211 -6 A88 88 0 0 0 211 170 L300 170 L300 -6 Z" fill="#f4f4f5"/>
      <path d="M211 0 A84 84 0 0 0 211 165" fill="none" stroke="#6cc4b8" stroke-width="4"/>
      <circle cx="232" cy="78" r="62" fill="none" stroke="rgba(58,140,165,0.10)" stroke-width="14"/>
    </svg>
    <div class="card__details">
      <div class="card__name">DANIEL FERRO</div>
      <div class="card__line">Brindle Oaks Orthodontics</div>
      <div class="card__line">123 Street Name</div>
      <div class="card__line">City, State Zip code</div>
      <div class="card__contact">
        <div><svg viewBox="0 0 10 10"><path d="M2 1 L4 1 L5 3 L4 4 Q5 6 6 6 L7 5 L9 6 L9 8 Q8 9 7 9 Q1 8 1 2 Q1 1 2 1 Z" fill="#fff"/></svg>555-014-2273</div>
        <div><svg viewBox="0 0 10 10"><rect x="1" y="2" width="8" height="6" fill="#fff"/><path d="M1 2 L5 5 L9 2" stroke="#3a8ca5" fill="none"/></svg>office@brindleoaksortho.com</div>
        <div><svg viewBox="0 0 10 10"><circle cx="5" cy="5" r="3.5" fill="none" stroke="#fff" stroke-width="1.2"/></svg>brindleoaksortho.com</div>
      </div>
      <div class="card__slogan">Creating "Tolvering" smiles<br>for Children &amp; Adults</div>
    </div>
    <div class="brand">
      <div class="brand__dot"></div>
      <div class="brand__name">Brindle Oaks</div>
      <div class="brand__tag">Pediatric Dentistry &amp; Orthodontics</div>
    </div>
  </section>

  <!-- Appointment card -->
  <section class="piece card card--appointment">
    <div class="island" role="img" aria-label="Illustrated island with palm trees, sand and sea, showing a small map to the office"></div>
    <div class="appt__title">SEE YOU AT YOUR NEXT APPOINTMENT!</div>
    <div class="appt__field" style="left:92px; top:36px;">For<span class="rule" style="width:178px;"></span></div>
    <div class="appt__field" style="left:110px; top:48px;">Date<span class="rule" style="width:74px;"></span>Time<span class="rule" style="width:66px;"></span></div>
    <div class="appt__pill">Specialist in Orthodontic &amp; Maxillofacial Orthopedics</div>
    <div class="brand">
      <div class="brand__dot"></div>
      <div class="brand__name">Brindle Oaks</div>
      <div class="brand__tag">Pediatric Dentistry &amp; Orthodontics</div>
    </div>
  </section>

  <!-- Envelope back -->
  <section class="piece envelope envelope--back">
    <svg width="530" height="90" viewBox="0 0 530 90">
      <path d="M0 0 L530 0 L530 48 Q520 74 494 76 L40 76 Q14 74 6 48 Z" fill="#3a8ca5"/>
    </svg>
    <div class="flap-mark"></div>
  </section>

  <!-- Envelope front -->
  <section class="piece envelope envelope--front">
    <div class="ghost-ring"></div>
    <div class="brand">
      <div class="brand__dot"></div>
      <div class="brand__name">Brindle Oaks</div>
      <div class="brand__tag">Pediatric Dentistry &amp; Orthodontics</div>
    </div>
    <div class="footer-band">
      Brindle Oaks Orthodontics<br>
      123 Street Name, City, State Zip code
      <div class="badge"></div>
    </div>
  </section>

</body>
</html>
```